eCommerce website for a DIY shop & communal center

We need a website for a business called The Maple Bench. The Maple Bench is both a shop and communal establishment where people with shared interests, especially in DIY (Do It Yourself) and crafting, can gather to shop for & work on projects while sharing ideas, equipment, supplies and knowledge. The shop is both brick & motor and online. The physical communal space provides workstations, equipment, tools and supplies and expertise for DIY lovers to create their projects.

Target Market(s)

Middle & upper class DIY enthusiasts, creative hobbyists, budding artists & small business owners

Industry/Entity Type

DIY, Arts & Crafts

Coding

Coded - Design and coding required

Number of Pages Required

5+ page

Requirements
Must have
• Menus to include 1. home page (with about us, operating hours, contacts, location, meet the team); 2. Bench activities (how to DIY at the Bench, booking, equipment & tools, house rules); 3. Bench events (events in the Bench, offsite events); 4. Resources (FAQs, tutorials, blogs, eBooks) and 5. Online shop
Nice to have
• Branding guidelines eg logo colours (see attachment) to influence design. Tillpost shop. Booking feature for activities & events at the Bench.

```html
<!DOCTYPE html>
<html lang="en">
<head>
<meta charset="utf-8">
<title>The Maple Bench</title>
<link href="https://fonts.googleapis.com/css2?family=Roboto:ital,wght@0,400;0,500;0,700;0,900;1,400;1,500&family=Allura&display=swap" rel="stylesheet">
<style>
:root{
  --orange:#f07a3c;
  --orange-light:#f59a4f;
  --blue:#2f8ad6;
  --ink:#1e1e1e;
  --body:#555;
  --muted:#777;
  --white:#fff;
  --footer:#0d0d0d;
  --wash-blue:#bfe1f3;
  --wash-pink:#f8d3c6;
}
*{margin:0;padding:0;box-sizing:border-box}
html,body{width:1200px;height:4898px;overflow:hidden}
body{position:relative;background:var(--white);font-family:"Roboto",Arial,sans-serif;color:var(--body)}
.abs{position:absolute}
.script{font-family:"Allura",cursive;font-weight:400;font-size:52px;line-height:1}
.script .o{color:var(--orange)} .script .b{color:var(--blue)}
.btn{position:absolute;display:flex;align-items:center;justify-content:center;border-radius:24px;background:linear-gradient(180deg,var(--orange-light),var(--orange));color:var(--white);font-size:14px;font-weight:700;letter-spacing:.5px;text-transform:uppercase}
.lead{position:absolute;text-align:center;font-size:15px;line-height:26px;color:var(--body)}
.photo{position:absolute}

/* header */
.header{position:absolute;left:0;top:0;width:1200px;height:99px;background:var(--white)}
.phone{position:absolute;left:101px;top:8px;display:flex;align-items:center;gap:12px;font-size:15px;font-weight:500;color:var(--ink)}
.phone .ring{width:34px;height:34px;border:1.5px solid #999;border-radius:50%;display:flex;align-items:center;justify-content:center}
.social-top{position:absolute;top:6px;right:101px;display:flex;gap:7px}
.social-top span{width:36px;height:36px;border:1.5px solid #999;border-radius:50%}
.nav a{position:absolute;top:63px;font-size:15px;font-weight:500;color:var(--ink);text-decoration:none;text-transform:uppercase}
.logo{position:absolute;left:530px;top:0;width:140px;height:136px;border-radius:0 0 70px 70px;background:var(--white);display:flex;align-items:center;justify-content:center;text-align:center;font-size:17px;font-weight:700;line-height:21px;color:var(--orange);z-index:3}

/* hero */
.hero{position:absolute;left:0;top:99px;width:1200px;height:566px;background:linear-gradient(90deg,#4a3a30 0%,#6d5040 40%,#8a6a55 70%,#5b4a40 100%)}
.hero h1{position:absolute;left:105px;top:200px;font-size:51px;line-height:55px;font-weight:900;color:var(--white);text-transform:uppercase}
.dots{position:absolute;left:556px;top:526px;display:flex;gap:13px}
.dots span{width:12px;height:12px;border:2px solid var(--white);border-radius:50%}
.dots span.on{background:var(--white)}

/* steps */
.step{position:absolute;top:917px;width:190px}
.step .frame{position:absolute;left:0;top:0;width:190px;height:190px;border:4px solid var(--blue)}
.step .pic{position:absolute;left:-4px;top:6px;width:196px;height:180px;border-radius:50%}
.step h3{position:absolute;top:212px;left:-40px;width:270px;text-align:center;font-size:15px;font-weight:500;font-style:italic;color:var(--ink)}
.step h3 em{color:var(--orange)}
.step p{position:absolute;top:248px;left:-30px;width:250px;text-align:center;font-size:11.5px;line-height:21px;color:var(--muted)}

/* about */
.about{position:absolute;left:0;top:1422px;width:1200px;height:480px;background:linear-gradient(90deg,#8a4a2c,#9c5634 50%,#8a4b2f)}
.about .crew{position:absolute;left:0;top:0;width:630px;height:480px;background:linear-gradient(180deg,#a45c3a,#7f4529)}
.about p{position:absolute;left:658px;top:150px;width:450px;font-size:14px;line-height:27px;color:#f4e6dc}

/* cards */
.card{position:absolute;top:2130px;width:320px;height:368px}
.caption{position:absolute;top:2517px;width:320px;text-align:center;font-size:20px;font-weight:500;color:var(--ink)}

/* hours */
.hours{position:absolute;left:270px;top:2879px}
.hours .row{display:flex;height:29.5px;font-size:14px;color:var(--ink)}
.hours .day{width:110px;text-align:right}
.hours .time{margin-left:82px;width:110px;text-align:center}

/* location */
.loc-text{position:absolute;left:643px;font-size:15px;color:var(--ink);line-height:29px}

/* team */
.member{position:absolute;top:3930px;width:320px;height:323px}
.name{position:absolute;top:4268px;width:320px;text-align:center;font-size:21px;font-weight:500;color:var(--ink)}
.role{position:absolute;top:4299px;width:320px;text-align:center;font-size:14px;color:var(--muted)}

/* footer */
.footer{position:absolute;left:0;top:4550px;width:1200px;height:348px;background:var(--footer);color:var(--white)}
.fcol{position:absolute;top:83px}
.fcol h4{font-size:15px;font-weight:700;text-transform:uppercase;margin-bottom:14px}
.fcol li{list-style:none;font-size:13px;line-height:28.5px}
.email{position:absolute;left:842px;top:112px;width:257px;height:40px;border-radius:20px;background:var(--white);color:#555;font-size:12px;padding:12px 16px}
.subscribe{position:absolute;left:842px;top:161px;width:257px;height:42px;border-radius:21px;background:var(--orange);color:var(--white);font-size:13px;font-weight:700;display:flex;align-items:center;justify-content:center}
.fsocial{position:absolute;left:852px;top:222px;display:flex;gap:7px}
.fsocial span{width:35px;height:35px;border-radius:50%;background:var(--white)}
.copy{position:absolute;left:0;top:310px;width:1200px;text-align:center;font-size:11.5px;color:#ddd}
</style>
</head>
<body>

<header class="header">
  <div class="phone"><span class="ring"><svg width="14" height="14" viewBox="0 0 24 24"><path d="M6.6 10.8a15 15 0 0 0 6.6 6.6l2.2-2.2a1 1 0 0 1 1-.25 11.4 11.4 0 0 0 3.6.57 1 1 0 0 1 1 1V20a1 1 0 0 1-1 1A17 17 0 0 1 3 4a1 1 0 0 1 1-1h3.5a1 1 0 0 1 1 1c0 1.25.2 2.45.57 3.57a1 1 0 0 1-.25 1z" fill="#777"/></svg></span>555 - 014 - 2290</div>
  <nav class="nav">
    <a style="left:101px">Home</a>
    <a style="left:194px">Bench Activities</a>
    <a style="left:380px">Bench Events</a>
    <a style="left:703px">Resources</a>
    <a style="left:849px">Online Shop</a>
    <a style="left:1007px">Contact Us</a>
  </nav>
  <div class="social-top"><span></span><span></span><span></span><span></span></div>
</header>
<div class="logo">The Maple<br>Bench</div>

<section class="hero">
  <div role="img" aria-label="Woman sketching on a tablet at a wooden workbench in a craft workshop" style="position:absolute;inset:0"></div>
  <h1>Tap into your<br>crafty side!</h1>
  <div class="btn" style="left:101px;top:334px;width:180px;height:44px">Get Started</div>
  <div class="dots"><span></span><span class="on"></span><span></span><span></span></div>
</section>

<h2 class="script abs" style="left:0;top:748px;width:1200px;text-align:center"><span class="o">Any</span> <span class="b">Craft</span> <span class="o">Any</span> <span class="b">Time</span></h2>
<p class="lead" style="left:270px;top:821px;width:660px">Lorem ipsum dolor sit amet, consectetur adipiscing elit, sed do eiusmod tempor incididunt ut labore et dolore magna aliqua. Quis ipsum suspendisse ultrices gravida.</p>

<div class="step" style="left:118px">
  <div class="frame"></div><div class="pic" role="img" aria-label="Customer choosing craft supplies from a shelf" style="background:linear-gradient(135deg,#8b8f96,#4c4f58)"></div>
  <h3><em>1.</em> Choose Your DIY</h3>
  <p>Lorem ipsum dol, consectetdipiscing elit, sed do eiusmod temporcididunt ut labore et dolore maalQuis ipsum suspendisse ultrices gravida.</p>
</div>
<div class="step" style="left:375px">
  <div class="frame"></div><div class="pic" role="img" aria-label="Laptop and craft tools on a desk for making a reservation" style="background:linear-gradient(135deg,#d8d2c8,#a39a8e)"></div>
  <h3><em>2.</em> Make a reservation or walk in</h3>
  <p>Lorem ipsum dol, consectetdipiscing elit, sed do eiusmod temporcididunt ut labore et dolore maalQuis ipsum suspendisse ultrices gravida.</p>
</div>
<div class="step" style="left:631px">
  <div class="frame"></div><div class="pic" role="img" aria-label="Group working together at a craft table" style="background:linear-gradient(135deg,#c9a78e,#8a6450)"></div>
  <h3><em>3.</em> Have fun!</h3>
  <p>Lorem ipsum dol, consectetdipiscing elit, sed do eiusmod temporcididunt ut labore et dolore maalQuis ipsum suspendisse ultrices gravida.</p>
</div>
<div class="step" style="left:888px">
  <div class="frame"></div><div class="pic" role="img" aria-label="Finished embroidered textile piece" style="background:linear-gradient(135deg,#b88a5c,#7a5234)"></div>
  <h3><em>4.</em> Take it home</h3>
  <p>Lorem ipsum dol, consectetdipiscing elit, sed do eiusmod temporcididunt ut labore et dolore maalQuis ipsum suspendisse ultrices gravida.</p>
</div>
<div class="btn" style="left:510px;top:1282px;width:178px;height:45px">Book a Project</div>

<section class="about">
  <div class="crew" role="img" aria-label="Four smiling people against a brick wall holding oversized tools and a colour swatch fan"></div>
  <h2 class="script abs" style="left:662px;top:86px;color:#fff">About Us</h2>
  <p>Sed ut perspiciatis unde omnis iste natus enluptatem accusantium doloremque laudantium, totam rem aperiam, eaque ipsa quae ab illo inventore veritatis et quasi architecto beatae e dicta sunt explicabo. Nemo enim ipsam voluptatem quia voluptas sit aspernatur aut odit aut fugit, sed quia consequuntur magni eos qui ratione voluptatem sequi nesciunt. Neque porro quisquam</p>
  <div class="btn" style="left:660px;top:346px;width:179px;height:46px">Learn More</div>
</section>

<svg class="abs" style="left:0;top:2330px" width="1200" height="340" aria-hidden="true">
  <defs><filter id="soft"><feGaussianBlur stdDeviation="30"/></filter></defs>
  <ellipse cx="200" cy="170" rx="260" ry="110" fill="var(--wash-blue)" filter="url(#soft)"/>
  <ellipse cx="620" cy="200" rx="280" ry="100" fill="var(--wash-pink)" filter="url(#soft)"/>
  <ellipse cx="1000" cy="140" rx="260" ry="120" fill="var(--wash-blue)" filter="url(#soft)"/>
</svg>
<h2 class="script abs" style="left:0;top:1988px;width:1200px;text-align:center"><span class="o">Featured</span> <span class="b">Projects</span></h2>
<p class="lead" style="left:270px;top:2048px;width:660px">Lorem ipsum dolor sit amet, consectetur adipiscing elit, sed do eiusmod tempor incididunt ut labore et dolore magna aliqua. Quis ipsum suspendisse ultrices gravida.</p>
<div class="card" style="left:101px;background:linear-gradient(180deg,#f0f0ee,#d9d4d0)" role="img" aria-label="Hanging wall art of red painted tiles on a driftwood branch"></div>
<div class="card" style="left:439px;background:linear-gradient(180deg,#eadfca,#d9c9ab)" role="img" aria-label="Fabric collage portrait with a colourful head wrap"></div>
<div class="card" style="left:780px;background:linear-gradient(180deg,#2a3442,#3c5a86)" role="img" aria-label="Painted sunset scene on a round wood slice"></div>
<div class="caption" style="left:101px">Sed ut perspiciatis und</div>
<div class="caption" style="left:439px">Sed ut perspiciatis und</div>
<div class="caption" style="left:780px">Sed ut perspiciatis und</div>

<svg class="abs" style="left:40px;top:2720px" width="580" height="440" aria-hidden="true">
  <defs><filter id="soft2"><feGaussianBlur stdDeviation="28"/></filter>
  <linearGradient id="peach" x1="0" y1="0" x2="1" y2="1"><stop offset="0" stop-color="#fbc9a4"/><stop offset="1" stop-color="#f7b6c0"/></linearGradient></defs>
  <ellipse cx="290" cy="210" rx="240" ry="160" fill="url(#peach)" filter="url(#soft2)"/>
</svg>
<h2 class="script abs" style="left:275px;top:2786px"><span class="o">Operating</span> <span class="b">Hours</span></h2>
<div class="hours">
  <div class="row"><span class="day">Monday</span><span class="time">09.30 – 20.00</span></div>
  <div class="row"><span class="day">Tuesday</span><span class="time">09.30 – 20.00</span></div>
  <div class="row"><span class="day">Wednesday</span><span class="time">09.30 – 20.00</span></div>
  <div class="row"><span class="day">Thursday</span><span class="time">09.30 – 20.00</span></div>
  <div class="row"><span class="day">Friday</span><span class="time">09.30 – 18.00</span></div>
  <div class="row"><span class="day">Saturday</span><span class="time">09.30 – 17.00</span></div>
  <div class="row"><span class="day">Sunday</span><span class="time">11.00 – 17.00</span></div>
</div>
<div class="photo" style="left:601px;top:2757px;width:498px;height:413px;background:linear-gradient(135deg,#b9bcc0,#6b6f74)" role="img" aria-label="Woodworker cutting a plank on a mitre saw"></div>

<svg class="abs" style="left:600px;top:3250px" width="600" height="420" aria-hidden="true">
  <defs><filter id="soft3"><feGaussianBlur stdDeviation="30"/></filter></defs>
  <ellipse cx="330" cy="190" rx="240" ry="130" fill="var(--wash-blue)" filter="url(#soft3)"/>
</svg>
<div class="photo" style="left:101px;top:3255px;width:498px;height:415px;background:linear-gradient(180deg,#3b6fb0 0%,#5d8fcf 40%,#d9bfa0 60%,#8a7a6a 100%)" role="img" aria-label="Exterior of the shop building with a dark awning"></div>
<h2 class="script abs" style="left:643px;top:3284px"><span class="o">Our</span> <span class="b">Location</span></h2>
<p class="loc-text" style="top:3356px">48 Alder Row Fernhill USA<br>30417</p>
<p class="loc-text" style="top:3428px;width:420px;font-size:14px">Sed ut perspiciatis unde omnis iste natus error sit voluptatem accusantium doloremque laudantium, totam rem aperiam, eaque ipsa quae ab</p>
<div class="btn" style="left:635px;top:3532px;width:183px;height:45px">Contact Us</div>

<svg class="abs" style="left:0;top:4120px" width="1200" height="360" aria-hidden="true">
  <defs><filter id="soft4"><feGaussianBlur stdDeviation="30"/></filter></defs>
  <ellipse cx="180" cy="170" rx="240" ry="100" fill="var(--wash-blue)" filter="url(#soft4)"/>
  <ellipse cx="600" cy="200" rx="260" ry="110" fill="var(--wash-pink)" filter="url(#soft4)"/>
  <ellipse cx="1000" cy="150" rx="250" ry="110" fill="var(--wash-blue)" filter="url(#soft4)"/>
</svg>
<h2 class="script abs" style="left:0;top:3768px;width:1200px;text-align:center"><span class="o">Meet</span> <span class="o">Our</span> <span class="o">Team</span></h2>
<p class="lead" style="left:142px;top:3826px;width:916px;font-size:14px">Sed ut perspiciatis unde omnis iste natus error sit voluptatem accusantium doloremque laudantium, totam rem aperiam, eaque ipsa quae ab illo inventore veritatis et quasi architecto beatae vitae dicta sunt explicabo. Nemo enim ipsam voluptatem quia voluptas sit aspernatur aut odit aut fugit, sed quia consequuntur magni dolores eos qui ratione voluptatem</p>
<div class="member" style="left:101px;background:linear-gradient(180deg,#d9d6d4,#b9c6d6)" role="img" aria-label="Portrait of a team member in a light blue shirt"></div>
<div class="member" style="left:439px;background:linear-gradient(180deg,#3e7fbf,#6fa3d6)" role="img" aria-label="Portrait of a team member with glasses"></div>
<div class="member" style="left:780px;background:linear-gradient(180deg,#e6e6e6,#9aa6b4)" role="img" aria-label="Portrait of a team member in a plaid shirt"></div>
<div class="name" style="left:101px">Owen Hartley</div>
<div class="name" style="left:439px">Owen Hartley</div>
<div class="name" style="left:780px">Owen Hartley</div>
<div class="role" style="left:101px">CEO</div>
<div class="role" style="left:439px">CEO</div>
<div class="role" style="left:780px">CEO</div>
<div class="btn" style="left:506px;top:4333px;width:186px;height:46px">Meet Our Team</div>

<footer class="footer">
  <div class="fcol" style="left:101px"><h4>About</h4><ul><li>Our Story</li><li>Press</li><li>Locations</li><li>Blog</li><li>Contact Us</li></ul></div>
  <div class="fcol" style="left:236px"><h4>Our Offering</h4><ul><li>Projects</li><li>Paint Burst Room</li><li>Parties</li><li>Classes</li></ul></div>
  <div class="fcol" style="left:420px"><h4>Other</h4><ul><li>Franchise</li><li>Gift Cards</li><li>FAQ</li><li>Refund Policy</li></ul></div>
  <div class="fcol" style="left:570px"><h4>Contact Us</h4><ul><li>48 Alder Row Fernhill USA</li><li>30417</li><li>555 - 014 - 2290</li><li>hello@maplebench.com</li></ul></div>
  <div class="fcol" style="left:842px"><h4>Get Updates &amp; Promos</h4></div>
  <div class="email">Email Address</div>
  <div class="subscribe">SUBSCRIBE</div>
  <div class="fsocial"><span></span><span></span><span></span><span></span></div>
  <p class="copy">Copyright © 2021 The Maple Bench. All rights reserved.</p>
</footer>

</body>
</html>
```